IT Company that provides secure IT solutions and services to our customers

We need business cards and a logo for a new IT Solutions company just created based in Kuala Lumpur, Malaysia. But will also be serving other countries in the region. We provide secure data, voice solutions on mobile platforms. Our first offering is encrypted voice and data solutions for IOS, Android, Windows and BlackBerry devices.

Target Market(s)

large organizations Govt, Police, Defence, Anti-corruption, Legal, highly regulated industries such as Health-care, Financial, Banking, Insurance,

Industry/Entity Type

Information Technology

Contact Information for Business Card

VelmoraNet (Logo - colour is ORVEX blue)Roshan Adeel Managing Director Kryption IT Sdn. Bhd.5th Floor, Block D, Wisma PLB,No.14 Jalan Seri Melor,50470, Kuala LumpurMalaysia

Font styles to use
Sans Serif

Colors
3176b5
ec1f27
fbed22

Requirements
Must have
• VelmoraNet all in Blue like ORVEX blue. A logo design perhaps a play of VN, K with a dangling T (colour can be any)
Nice to have
• I want a clean crisp card, not too busy, easy to read.

```html
<!DOCTYPE html>
<html lang="en">
<head>
<meta charset="utf-8">
<title>VelmoraNet Business Card</title>
<link href="https://fonts.googleapis.com/css2?family=Open+Sans:wght@400;600;700&display=swap" rel="stylesheet">
<style>
  :root {
    --backdrop: #2a2a2b;
    --card: #141416;
    --brand-blue: #1f62c4;
    --text-light: #e6e6e6;
    --divider: #1d4f9c;
  }
  * { margin: 0; padding: 0; box-sizing: border-box; }
  html, body {
    width: 1200px; height: 900px; overflow: hidden;
    background: var(--backdrop);
    font-family: "Open Sans", sans-serif;
  }
  .stage {
    position: relative; width: 1200px; height: 900px;
  }
  .card {
    position: absolute;
    width: 500px; height: 290px;
    top: 305px;
    background: var(--card);
    border-radius: 26px;
    box-shadow: 0 14px 30px rgba(0,0,0,0.45);
  }
  .card--contact { left: 80px; }
  .card--brand { left: 620px; }

  /* contact side */
  .contact-mark {
    position: absolute; left: 34px; top: 0; bottom: 0; width: 210px;
    display: flex; align-items: center; gap: 12px;
  }
  .mark-square {
    width: 26px; height: 26px; border: 3px solid var(--brand-blue); flex: none;
  }
  .mark-name {
    color: var(--brand-blue); font-weight: 700; font-size: 22px; letter-spacing: 0.2px;
  }
  .contact-divider {
    position: absolute; left: 252px; top: 62px; height: 166px; width: 1px;
    background: var(--divider);
  }
  .contact-details {
    position: absolute; left: 272px; top: 70px; right: 16px;
    font-size: 13.5px; line-height: 1.38; color: var(--text-light);
  }
  .person-name { color: var(--brand-blue); font-weight: 600; font-size: 15px; }
  .person-role { margin-bottom: 10px; }
  .company-name { color: var(--brand-blue); font-weight: 700; font-size: 15px; }

  /* brand side */
  .brand-lockup {
    position: absolute; inset: 0;
    display: flex; align-items: center; justify-content: center; gap: 14px;
  }
  .brand-square {
    width: 40px; height: 40px; border: 3px solid var(--brand-blue);
  }
  .brand-name {
    color: var(--brand-blue); font-weight: 700; font-size: 40px; letter-spacing: 0.3px;
  }
</style>
</head>
<body>
<main class="stage">
  <section class="card card--contact">
    <div class="contact-mark">
      <span class="mark-square"></span>
      <span class="mark-name">VelmoraNet</span>
    </div>
    <div class="contact-divider"></div>
    <div class="contact-details">
      <p class="person-name">Roshan Adeel</p>
      <p class="person-role">Managing Director</p>
      <p class="company-name">Velmora Net</p>
      <p class="address">Sdn. Bhd.5th Floor, Block D,<br>Wisma PLB,No.14 Jalan Seri Melor,<br>50470, Kuala Lumpur<br>Malaysia</p>
    </div>
  </section>

  <section class="card card--brand">
    <div class="brand-lockup">
      <span class="brand-square"></span>
      <span class="brand-name">VelmoraNet</span>
    </div>
  </section>
</main>
</body>
</html>
```